Lantern Hollow Brewing Company New Website with Food Ordering

We need a wordpress-based website for a local brewery & pizza kitchen. The final design will have 6 primary pages: home page, order pizza, our beers, visit us, about us, merch store. The website must integrate with tillpoint for kitchens for online ordering for takeout and delivery. It will also a feature a selection of beers and help customers navigate to the brewery and find hours of operation. The existing website is lanternhollowbrew.example. This is a very old website.

Industry/Entity Type

Brewery and food service

Coding

Coded - Design and coding required

Number of Pages Required

5+ page

Font styles to use
Sans Serif

Requirements
Must have
• ability to integrate seamlessly with tillpoint for kitchens, 21+ age gate
Nice to have
• see attached pdf

```html
<!DOCTYPE html>
<html lang="en">
<head>
<meta charset="utf-8">
<title>Lantern Hollow Brewing Company</title>
<link href="https://fonts.googleapis.com/css2?family=Graduate&family=Roboto:wght@400;500;700&family=Lato:wght@400&display=swap" rel="stylesheet">
<style>
:root{
  --red:#c8102e;
  --ink:#231f20;
  --white:#ffffff;
  --text:#555555;
  --line:#5a5557;
  --photo-warm:#9c3b2c;
  --photo-deep:#5a2a22;
  --gold:#f7d12a;
}
*{box-sizing:border-box;margin:0;padding:0}
html,body{width:685px;height:1200px;overflow:hidden;background:var(--white)}
body{position:relative;font-family:'Roboto',sans-serif;color:var(--ink)}
.slab{font-family:'Graduate',serif;font-weight:400}

/* header */
.site-header{position:absolute;left:0;top:0;width:685px;height:53px;background:var(--white)}
.nav-link{position:absolute;top:23px;font-size:8.3px;font-weight:500;color:var(--ink)}
.brand-mark{position:absolute;left:311px;top:1px;width:59px;height:52px;background:var(--ink);display:flex;align-items:center;justify-content:center}
.brand-mark span{background:var(--red);color:var(--white);font-weight:700;font-size:8px;line-height:1.1;text-align:center;width:51px;height:44px;display:flex;align-items:center;justify-content:center}
.promo-badge{position:absolute;left:560px;top:7px;width:60px;height:42px;border-radius:50%;background:var(--gold)}

/* hero */
.hero-photo{position:absolute;left:0;top:53px;width:685px;height:368px;background:linear-gradient(120deg,var(--photo-warm) 0%,#b2523a 45%,var(--photo-deep) 100%)}
.hero-badge{position:absolute;left:360px;top:123px;width:260px;height:228px}
.hero-title{position:absolute;left:360px;top:178px;width:260px;text-align:center;color:var(--white);font-size:19.5px;line-height:24.5px}
.btn{position:absolute;display:flex;align-items:center;justify-content:center;gap:6px;border-radius:14px;font-weight:700;font-size:8.3px;color:var(--white)}
.btn-dark{background:var(--ink)}
.btn-red{background:var(--red)}
.btn svg{width:8px;height:8px}

.quick-bar{position:absolute;left:64px;top:389px;width:557px;height:65px;background:var(--white);border-radius:10px;box-shadow:0 2px 8px rgba(0,0,0,.12)}
.pill{position:absolute;top:19px;width:108px;height:28px;border-radius:14px;border:1px solid var(--red);color:var(--red);display:flex;align-items:center;justify-content:center;font-family:'Graduate',serif;font-size:8.3px}
.pill.is-active{background:var(--red);color:var(--white)}

/* about */
.about-title{position:absolute;left:64px;top:504px;font-size:14.6px;color:var(--ink)}
.rule{position:absolute;height:1.5px;width:24px;background:var(--red)}
.about-copy{position:absolute;left:64px;top:544px;width:259px;font-family:'Lato',sans-serif;font-weight:400;font-size:8.1px;line-height:13.2px;color:var(--text);text-align:justify}
.about-copy p+p{margin-top:13px}
.pizza-photo{position:absolute;left:368px;top:507px;width:253px;height:222px;background:radial-gradient(circle at 50% 45%,#d9a441 0%,#a8342a 55%,#6e2418 100%)}

/* call band */
.call-band{position:absolute;left:0;top:784px;width:685px;height:181px;background:linear-gradient(90deg,#c4112f,#b80f2b 50%,#c4112f)}
.call-title{position:absolute;left:0;width:685px;top:815px;text-align:center;color:var(--white);font-size:14.5px}
.call-copy{position:absolute;left:64px;top:854px;width:557px;text-align:justify;text-align-last:center;color:var(--white);font-size:8.3px;line-height:13.2px}
.phone-dot{position:absolute;left:277px;top:912px;width:21px;height:21px;border-radius:50%;background:var(--ink);display:flex;align-items:center;justify-content:center}
.call-label{position:absolute;left:313px;top:910px;color:var(--white);font-size:6.8px;font-weight:700}
.call-number{position:absolute;left:313px;top:919px;color:var(--white);font-size:12px;font-weight:500}

/* footer */
.site-footer{position:absolute;left:0;top:965px;width:685px;height:235px;background:var(--ink)}
.footer-brand{position:absolute;left:78px;top:1010px;width:90px;height:79px;background:#3a3536;display:flex;align-items:center;justify-content:center}
.footer-brand span{width:78px;height:62px;background:var(--red);color:var(--white);font-weight:700;font-size:10px;line-height:1.15;text-align:center;display:flex;align-items:center;justify-content:center}
.social{position:absolute;top:1099px;width:19px;height:19px;border-radius:50%;background:var(--red)}
.divider{position:absolute;top:1003px;width:1px;height:115px;background:var(--line)}
.footer-head{position:absolute;top:1010px;color:var(--white);font-size:8.1px;font-weight:500}
.footer-rule{position:absolute;top:1026px;width:15px;height:1px;background:var(--white)}
.link-list{position:absolute;list-style:none;color:var(--white);font-size:8.3px;font-weight:400}
.link-list li{height:17.6px;display:flex;align-items:center}
.link-list li::before{content:"»";width:15px;font-size:9px}
.contact-row{position:absolute;left:344px;display:flex;align-items:center;gap:10px;color:var(--white);font-size:7px;font-weight:400}
.contact-icon{width:19px;height:19px;border-radius:50%;border:1px solid var(--white);display:flex;align-items:center;justify-content:center;flex:none}
.contact-row.strong{font-size:8.5px;font-weight:500}
.bottom-rule{position:absolute;left:60px;top:1148px;width:566px;height:1px;background:var(--line)}
.copyright{position:absolute;left:0;width:685px;top:1170px;text-align:center;color:var(--white);font-size:8.1px}
</style>
</head>
<body>

<header class="site-header">
  <span class="nav-link" style="left:65px">THE KITCHEN</span>
  <span class="nav-link" style="left:140px">OUR BEERS</span>
  <span class="nav-link" style="left:207px">VISIT US</span>
  <div class="brand-mark"><span>Lantern Hollow</span></div>
  <span class="nav-link" style="left:432px">ABOUT US</span>
  <span class="nav-link" style="left:495px">MERCH</span>
  <div class="promo-badge" role="img" aria-label="Promo starburst graphic announcing Try Hazel"></div>
</header>

<div class="hero-photo" role="img" aria-label="Photo of a Detroit-style square pizza and glasses of beer on a red picnic table"></div>
<svg class="hero-badge" viewBox="0 0 532 466" aria-hidden="true">
  <polygon points="0,58 264,0 532,58 532,410 264,466 0,410" fill="var(--ink)"/>
  <polygon points="30,86 264,50 502,86 502,384 264,416 30,384" fill="var(--red)"/>
</svg>
<h1 class="hero-title slab">SQUARE PIZZA<br>AND GREAT BEER IN<br>PORTLAND, MAINE</h1>
<div class="btn btn-dark" style="left:444px;top:264px;width:94px;height:27px">ORDER ONLINE
  <svg viewBox="0 0 16 16"><path d="M0 1h3l1 3h12l-2 7H5L2 3H0z M5 13a1.5 1.5 0 1 0 .01 0z M13 13a1.5 1.5 0 1 0 .01 0z" fill="var(--white)"/></svg>
</div>

<nav class="quick-bar">
  <span class="pill is-active" style="left:43px">ORDER ONLINE</span>
  <span class="pill" style="left:164px">VISIT US</span>
  <span class="pill" style="left:285px">OUR BEERS</span>
  <span class="pill" style="left:406px">ABOUT US</span>
</nav>

<h2 class="about-title slab">WHAT IS DETROIT-STYLE PIZZA?</h2>
<div class="rule" style="left:64px;top:531px"></div>
<div class="about-copy">
  <p>Lantern Hollow Brewing was founded on the idea that at the base of human community, you will find good people and good beer. Born on the edge of Portland, Maine in 2014, our focus has always been on building a business we are proud of that makes a difference in our community one beer at a time. Thanks for joining us on that journey.</p>
  <p>Our new Pizza Kitchen is now open! Please keep an eye on our social media as we make announcements there and share delicious photos of Detroit-style square pizza. The menu focuses on the square pizza that Mark &amp; Lena grew up eating in Detroit. Chef Owen also brings his love of beer and food pairing to the kitchen with selections</p>
</div>
<div class="btn btn-red" style="left:64px;top:702px;width:95px;height:27px">ORDER ONLINE
  <svg viewBox="0 0 16 16"><path d="M0 1h3l1 3h12l-2 7H5L2 3H0z M5 13a1.5 1.5 0 1 0 .01 0z M13 13a1.5 1.5 0 1 0 .01 0z" fill="var(--white)"/></svg>
</div>
<div class="btn btn-dark" style="left:167px;top:702px;width:109px;height:27px">VIEW FULL MENU
  <svg viewBox="0 0 16 16"><circle cx="8" cy="8" r="8" fill="var(--white)"/><path d="M6 4l4 4-4 4" stroke="var(--ink)" stroke-width="2.2" fill="none"/></svg>
</div>
<div class="pizza-photo" role="img" aria-label="Close-up photo of a pepperoni Detroit-style pizza with scallions on a cooling rack"></div>

<div class="call-band" role="img" aria-label="Red-tinted photo of beer cans in the background"></div>
<h2 class="call-title slab">QUESTIONS? GIVE US A CALL</h2>
<div class="rule" style="left:331px;top:840px;background:var(--white)"></div>
<p class="call-copy">Sed ut perspiciatis unde omnis iste natus error sit voluptatem accusantium doloremque laudantium, totam rem aperiam, eaque ipsa quae ab illo inventore veritatis et quasi architecto beatae vitae dicta sunt explicabo. Nemo enim ipsam voluptatem quia voluptas sit aspernatur aut odit aut fugit, sed quia consequuntur magni dolores eos qui ratione voluptatem sequi nesciunt.</p>
<div class="phone-dot"><svg width="9" height="9" viewBox="0 0 16 16"><path d="M3 1l3 3-2 2c1 2 4 5 6 6l2-2 3 3-2 2C7 15 1 9 1 3z" fill="var(--white)"/></svg></div>
<span class="call-label">CALL US TODAY !</span>
<span class="call-number">+1 207-555-0148</span>

<footer class="site-footer"></footer>
<div class="footer-brand"><span>Lantern<br>Hollow</span></div>
<span class="social" style="left:82px"></span>
<span class="social" style="left:103px"></span>
<span class="social" style="left:125px"></span>
<span class="social" style="left:147px"></span>

<div class="divider" style="left:191px"></div>
<div class="divider" style="left:318px"></div>
<div class="divider" style="left:500px"></div>

<span class="footer-head" style="left:224px">QUICK LINKS</span>
<div class="footer-rule" style="left:224px"></div>
<ul class="link-list" style="left:224px;top:1035px">
  <li>Home</li><li>The Kitchen</li><li>Our Beers</li><li>Visit Us</li><li>About Us</li>
</ul>

<span class="footer-head" style="left:344px">CONTACT US</span>
<div class="footer-rule" style="left:344px"></div>
<div class="contact-row" style="top:1037px">
  <span class="contact-icon"><svg width="7" height="9" viewBox="0 0 12 16"><path d="M6 0a6 6 0 0 0-6 6c0 4 6 10 6 10s6-6 6-10a6 6 0 0 0-6-6zm0 8a2 2 0 1 1 0-4 2 2 0 0 1 0 4z" fill="var(--white)"/></svg></span>
  <span>PO Box 412 Ca 95610<br>United States</span>
</div>
<div class="contact-row strong" style="top:1070px">
  <span class="contact-icon"><svg width="8" height="8" viewBox="0 0 16 16"><path d="M3 1l3 3-2 2c1 2 4 5 6 6l2-2 3 3-2 2C7 15 1 9 1 3z" fill="var(--white)"/></svg></span>
  <span>+1 207-555-0148</span>
</div>
<div class="contact-row" style="top:1101px">
  <span class="contact-icon"><svg width="8" height="7" viewBox="0 0 16 12"><path d="M0 0h16v12H0z" fill="var(--white)"/><path d="M0 0l8 6 8-6" stroke="var(--ink)" stroke-width="1.5" fill="none"/></svg></span>
  <span>beerme@lanternhollowbrew.example</span>
</div>

<span class="footer-head" style="left:526px">OTHER LINKS</span>
<div class="footer-rule" style="left:526px"></div>
<ul class="link-list" style="left:526px;top:1035px">
  <li>Merch</li><li>Help Service</li><li>Terms &amp; Conditions</li><li>Privacy Plocy</li><li>FAQ</li>
</ul>

<div class="bottom-rule"></div>
<p class="copyright">© 2022 Lantern Hollow Brew. All Rights Reserved</p>

</body>
</html>
```